Vibrant, yet professional, stationery set and other designs required.

I need to source a fantastic designer for a new project as part of my company using a new logo designed via sketch harbor.

**UPDATE** I am not looking for just 'fine' design that will suffice. I am looking for something great.

We are a life assurance brokerage based in Dublin, Ireland and BrightRoost.ie is our new website aimed at providing services for young families in Ireland. We are hoping to be the 'Velro' level of service providers in this area and I am looking for the quality of design to reflect this :-) Hopefully that makes sense!

I have a preference for straight lines over curves and waves.

I need...

1. Business card
2. Letterhead
3. Banner (for printing - 76cm X 305cm)
4. Car branding for KORVA 9 (2014 sport model) I believe the templates are freely available online.

Target Market(s)

Parents in Ireland - Aged 27 to 50.

Industry/Entity Type

Financial Planning

Colors

Designer to choose colors to be used in the design.

Requirements
Must have
• All of the items listed in the description above. I like clean, bright, legible, vibrant and professional design.
Should not have
• No silly or 'cheap' looking designs. This is a professional company looking to provide a professional service.

```html
<!DOCTYPE html>
<html lang="en">
<head>
<meta charset="utf-8">
<title>BrightRoost.ie Business Card</title>
<link rel="stylesheet" href="https://fonts.googleapis.com/css2?family=Open+Sans:wght@400;600;700&display=swap">
<style>
  :root {
    --slate: #7b9197;
    --paper: #f7f8f8;
    --ink: #3a3d3f;
    --blue: #1fa8df;
    --green: #8dc21f;
    --orange: #f26b1d;
    --backdrop: #e9e6e1;
    --white: #f4f6f8;
  }
  * { box-sizing: border-box; margin: 0; padding: 0; }
  html, body {
    width: 1200px; height: 800px; overflow: hidden;
    background: var(--backdrop);
    font-family: "Open Sans", Arial, sans-serif;
  }
  .card {
    position: absolute; top: 245px;
    width: 540px; height: 310px;
    box-shadow: 0 6px 18px rgba(0,0,0,.12);
    overflow: hidden;
  }
  .card-front { left: 50px; background: var(--paper); }
  .card-back { left: 610px; background: var(--slate); }

  .side-band {
    position: absolute; left: 0; top: 0; bottom: 0; width: 62px;
    background: var(--slate);
  }
  .brand-square {
    position: absolute; left: 48px; top: 34px;
    width: 28px; height: 28px; background: var(--orange);
  }
  .contact-block {
    position: absolute; left: 98px; top: 30px;
    width: 180px;
    color: var(--ink);
  }
  .person-name {
    font-size: 19px; font-weight: 600; color: var(--blue);
    letter-spacing: .3px; line-height: 1.1;
  }
  .person-role {
    font-size: 15px; font-weight: 400; color: var(--green);
    margin-bottom: 22px;
  }
  .address { font-size: 14px; line-height: 1.35; margin-bottom: 12px; white-space: nowrap; }
  .contact-list { list-style: none; font-size: 14px; line-height: 1.45; }
  .contact-list li { display: flex; align-items: center; gap: 9px; white-space: nowrap; }
  .contact-list svg { width: 12px; height: 12px; flex: none; fill: var(--blue); }

  .brand-name {
    font-weight: 700; letter-spacing: -1px; line-height: 1;
    white-space: nowrap;
  }
  .card-front .brand-name {
    position: absolute; right: 30px; top: 150px;
    font-size: 32px; color: var(--slate);
  }
  .card-back .brand-name {
    position: absolute; left: 0; right: 0; top: 50%;
    transform: translateY(-50%);
    text-align: center; font-size: 64px; color: var(--white);
  }
</style>
</head>
<body>
  <section class="card card-front" aria-label="Business card front">
    <div class="side-band"></div>
    <div class="brand-square"></div>
    <div class="contact-block">
      <p class="person-name">NORA KEANE</p>
      <p class="person-role">CEO/FOUNDER</p>
      <p class="address">42 Larkfield Row<br>Dunmore, Leinster 20817</p>
      <ul class="contact-list">
        <li><svg viewBox="0 0 12 12"><path d="M1 4c0-2 2-3 5-3s5 1 5 3H8V3H4v1zM2 5h8l1 6H1z"/></svg>614 209 5381</li>
        <li><svg viewBox="0 0 12 12"><path d="M3 0h6v12H3zM4 1.5v8h4v-8z"/></svg>872 315 0462</li>
        <li><svg viewBox="0 0 12 12"><path d="M3 0h6v4H3zM0 5h12v5H10v2H2v-2H0zM3 8v3h6V8z"/></svg>455 730 1286</li>
        <li><svg viewBox="0 0 12 12"><path d="M0 2h12v1L6 7 0 3zM0 4.5l6 4 6-4V10H0z"/></svg>hello@brightroost.ie</li>
        <li><svg viewBox="0 0 12 12"><circle cx="6" cy="6" r="6"/></svg>www.brightroost.ie</li>
      </ul>
    </div>
    <p class="brand-name">brightroost.ie</p>
  </section>

  <section class="card card-back" aria-label="Business card back">
    <p class="brand-name">brightroost.ie</p>
  </section>
</body>
</html>
```